Building company buisness cards

We are looking for a sharp modern new look for our business cards.
We are a New Zealand based company that specialises in house and land packages.
We have attached a photo of the current logo and would like to see if it can be improved somehow if needed.
We are open to any colours but we have chosen green at this stage.
Feel free to change the font and make the logo smarter looking.
Play with the colours and see what looks best.

We want a card that looks so good know one will want to throw it away!

Target Market(s)

Home buyers

Industry/Entity Type

Building

Contact Information for Business Card

Derek Tolvane
0217394062
dtolvane@quillmarkhomesteads.co.nz
quillmarkhomesteads.co.nz

Font styles to use
Serif
Sans Serif

Colors

Designer to choose colors to be used in the design.

Requirements
Must have
• Logo and company name on one side, details on the other side
Nice to have
• Color codes for the original green are HEX #4a8028, RGB(74,128,40), CMYK(42,0,69,50)
• Round corners, Raised and/or spot UV

```html
<!DOCTYPE html>
<html lang="en">
<head>
<meta charset="utf-8">
<title>Quillmark Homesteads – Business Cards</title>
<link rel="stylesheet" href="https://fonts.googleapis.com/css2?family=Lato:wght@700&family=Open+Sans:wght@400&family=Montserrat:wght@800&display=swap">
<style>
  :root {
    --brand-green: #4a8028;
    --name-green: #3f7a22;
    --card-white: #ffffff;
    --backdrop: #5b5b5b;
    --ink: #2a2a2a;
    --rule-soft: rgba(255,255,255,0.35);
  }
  * { margin: 0; padding: 0; box-sizing: border-box; }
  html, body { width: 1200px; height: 802px; overflow: hidden; }
  body { background: var(--backdrop); position: relative; }

  .card {
    position: absolute;
    top: 274px;
    width: 442px;
    height: 264px;
    box-shadow: 2px 3px 6px rgba(0,0,0,0.45);
  }
  .card--details { left: 136px; background: var(--card-white); }
  .card--brand { left: 624px; background: var(--brand-green); }

  /* details side */
  .brand-mark {
    position: absolute;
    left: 22px;
    top: 92px;
    width: 116px;
    display: flex;
    align-items: center;
    gap: 8px;
    font-family: "Lato", sans-serif;
    font-weight: 700;
    font-size: 17px;
    line-height: 1.15;
    color: var(--brand-green);
  }
  .brand-mark__square {
    flex: none;
    width: 14px;
    height: 14px;
    background: var(--brand-green);
  }
  .divider {
    position: absolute;
    left: 152px;
    top: 90px;
    width: 1px;
    height: 85px;
    background: var(--brand-green);
  }
  .person-name {
    position: absolute;
    left: 164px;
    top: 96px;
    font-family: "Lato", sans-serif;
    font-weight: 700;
    font-size: 16px;
    letter-spacing: -0.2px;
    color: var(--name-green);
  }
  .contact-list {
    position: absolute;
    left: 164px;
    top: 128px;
    list-style: none;
    font-family: "Open Sans", sans-serif;
    font-size: 12px;
    line-height: 15.5px;
    color: var(--ink);
  }
  .contact-list li { display: flex; align-items: center; gap: 4px; white-space: nowrap; }
  .contact-list svg { width: 10px; height: 10px; flex: none; fill: var(--brand-green); }

  /* brand side */
  .wordmark {
    position: absolute;
    left: 0;
    right: 0;
    top: 72px;
    text-align: center;
    font-family: "Montserrat", sans-serif;
    font-weight: 800;
    color: var(--card-white);
    line-height: 1;
  }
  .wordmark__top { display: block; font-size: 28px; letter-spacing: -0.5px; }
  .wordmark__bottom { display: block; font-size: 35px; letter-spacing: -1px; margin-top: 4px; }
  .wordmark-rule {
    position: absolute;
    left: 192px;
    top: 200px;
    width: 62px;
    height: 1px;
    background: var(--rule-soft);
  }
</style>
</head>
<body>

<section class="card card--details" aria-label="Card back with contact details">
  <div class="brand-mark">
    <span class="brand-mark__square"></span>
    <span>quillmark homesteads</span>
  </div>
  <div class="divider"></div>
  <h1 class="person-name">DEREK TOLVANE</h1>
  <ul class="contact-list">
    <li>
      <svg viewBox="0 0 10 10" aria-hidden="true"><path d="M1 3.2C1 2 2 1.5 5 1.5S9 2 9 3.2L7.4 3.8 7 2.9H3L2.6 3.8ZM2.5 4.3h5l1 4.2h-7ZM5 5.2a1.2 1.2 0 1 0 0.01 0Z"/></svg>
      0217394062
    </li>
    <li>
      <svg viewBox="0 0 10 10" aria-hidden="true"><path d="M1 2.5h8v5H1ZM1.6 3l3.4 2.6L8.4 3Z" fill-rule="evenodd"/></svg>
      dtolvane@quillmarkhomesteads.co.nz
    </li>
    <li>
      <svg viewBox="0 0 10 10" aria-hidden="true"><circle cx="5" cy="5" r="4.3"/><path d="M3 3.2l1.6.5.2 1.5-1.3.8ZM6 5.6l1.5.4-.6 1.8-1.2-.8Z" fill="#fff"/></svg>
      www.quillmarkhomesteads.co.nz
    </li>
  </ul>
</section>

<section class="card card--brand" aria-label="Card front with company name">
  <div class="wordmark">
    <span class="wordmark__top">quillmark</span>
    <span class="wordmark__bottom">homesteads.</span>
  </div>
  <div class="wordmark-rule"></div>
</section>

</body>
</html>
```